Brindle Water - 500ml

to create a water bottle packaging similar to L'onde Claire design. Bottle should be blue similar to PURE FLOW but change the design/logo to Brindle. Wording should be similar just different design and logo. Thanks.

Colors
0054AA
0677BA
7BADD7
CADEEF
E8F1F8

Requirements
Must have
• Bottle must not be in plastic bottles. They are made in a carton instead - see PURE FLOW for reference.

```html
<!DOCTYPE html>
<html lang="en">
<head>
<meta charset="UTF-8">
<title>Brindle Water – 500 ml carton front panel</title>
<link rel="stylesheet" href="https://fonts.googleapis.com/css2?family=Anton&family=Oswald:wght@400;600&display=swap">
<style>
  :root {
    --page-bg: #eef2f5;
    --carton-blue: #38ade2;
    --carton-deep: #0677ba;
    --title-tint: #a9def6;
    --ink-white: #ffffff;
    --snow: #e8f1f8;
    --mist: #cadeef;
    --sky: #7badd7;
  }
  * { margin: 0; padding: 0; box-sizing: border-box; }
  html, body {
    width: 1200px;
    height: 3000px;
    overflow: hidden;
    background: var(--page-bg);
  }
  .carton-front {
    position: absolute;
    left: 150px;
    top: 300px;
    width: 900px;
    height: 2400px;
    background: var(--carton-blue);
    overflow: hidden;
    box-shadow: 0 20px 60px rgba(6, 119, 186, 0.18);
  }
  .top-seal {
    position: absolute;
    left: 0; top: 0;
    width: 100%;
    height: 70px;
    background: var(--carton-deep);
    opacity: 0.35;
  }
  .mountain-art {
    position: absolute;
    left: 0;
    bottom: 0;
    width: 100%;
    height: 980px;
    background: linear-gradient(to bottom, var(--carton-blue) 0%, var(--sky) 30%, var(--mist) 55%, var(--snow) 75%, var(--ink-white) 100%);
  }
  .product-title {
    position: absolute;
    left: 40px;
    bottom: 110px;
    writing-mode: vertical-rl;
    transform: rotate(180deg);
    font-family: "Anton", sans-serif;
    font-size: 270px;
    line-height: 1;
    letter-spacing: 6px;
    color: var(--title-tint);
    white-space: nowrap;
  }
  .brand-block {
    position: absolute;
    left: 440px;
    top: 220px;
    text-align: center;
    width: 380px;
    color: var(--ink-white);
    font-family: "Oswald", sans-serif;
  }
  .brand-name {
    font-size: 96px;
    font-weight: 600;
    line-height: 1;
  }
  .brand-tagline {
    margin-top: 10px;
    font-size: 20px;
    letter-spacing: 4px;
    font-weight: 400;
  }
  .claim-block {
    position: absolute;
    left: 450px;
    top: 560px;
    color: var(--ink-white);
    font-family: "Oswald", sans-serif;
  }
  .claim-percent {
    font-size: 58px;
    font-weight: 600;
    line-height: 1.1;
  }
  .claim-source {
    font-size: 58px;
    font-weight: 600;
    letter-spacing: 3px;
    line-height: 1.1;
  }
  .claim-note {
    margin-top: 70px;
    font-size: 30px;
    font-weight: 600;
    line-height: 1.3;
    letter-spacing: 1px;
  }
  .volume-drop {
    position: absolute;
    left: 500px;
    top: 1000px;
    width: 260px;
    height: 360px;
  }
  .volume-label {
    position: absolute;
    left: 0; top: 165px;
    width: 100%;
    text-align: center;
    font-family: "Oswald", sans-serif;
    font-weight: 600;
    font-size: 64px;
    line-height: 1.05;
    color: var(--carton-blue);
  }
</style>
</head>
<body>
  <main class="carton-front">
    <div class="top-seal"></div>
    <div class="mountain-art" role="img" aria-label="Snow-capped mountain range illustration in white and pale blue"></div>
    <h1 class="product-title">PURE FLOW</h1>

    <header class="brand-block">
      <div class="brand-name">Brindle</div>
      <div class="brand-tagline">PURE SPRING WATER</div>
    </header>

    <section class="claim-block">
      <p class="claim-percent">100%</p>
      <p class="claim-source">SPRING WATER</p>
      <p class="claim-note">SUSTAINABLY SOURCED WATER<br>IN A PLANT-BASED<br>CARTON</p>
    </section>

    <div class="volume-drop">
      <svg width="260" height="360" viewBox="0 0 260 360" aria-hidden="true">
        <path d="M130 8 C 160 80 244 170 244 236 A 114 114 0 0 1 16 236 C 16 170 100 80 130 8 Z" fill="#ffffff"/>
      </svg>
      <div class="volume-label">500<br>ML</div>
    </div>
  </main>
</body>
</html>
```